Crumb of Maple 2022- CW poster ads

Design for our Crumb of Maple Event
Designs 3 designs for Chirp Wall Banner, posts and social Media ads
Each can look the same just different subjects on each
1. Design We're Back!
The Crumb Of Maple Is Back!
Fernquay County’s Premier Food, Wine and Brew Event
August 14th
Vendor and ticket info at https://brimfulmaplefq.com/

2. Vendors be a part of the event
The Crumb of Maple is Back!
August 14th 2020
Vendors sign up today at
Vendor info at https://brimfulmaplefq.com/

3. Sponsor info
The Crumb Of Maple
August 14th 2022
Check out our great Sponsorship opportunities
Sponsor info at https://brimfulmaplefq.com/

Target Market(s)

Foodies, wine and beer enthusists

Industry/Entity Type

Farm to fork, fresh in season and local

Colors
00AB8E
00BBA5
67D7C9
C6EFE9
E9F9F6

Requirements
Should not have
• no fast food looking photos

```html
<!DOCTYPE html>
<html lang="en">
<head>
<meta charset="utf-8">
<title>Crumb of Maple 2022 – Chirp Wall Banners</title>
<link rel="stylesheet" href="https://fonts.googleapis.com/css2?family=Roboto+Slab:wght@700&family=Roboto:wght@400&family=Lobster&display=swap">
<style>
  :root{
    --backdrop:#2a4227;
    --cream-light:#f7e9bd;
    --cream-dark:#ecd595;
    --ink-green:#2e3b22;
    --ink:#1e1e1a;
    --accent-red:#d53a26;
    --accent-red-dark:#a8281a;
    --label:#ffffff;
  }
  *{margin:0;padding:0;box-sizing:border-box}
  html,body{width:1200px;height:789px;overflow:hidden;background:var(--backdrop)}
  .board{position:relative;width:1200px;height:789px}
  .banner{position:absolute;left:270px;width:630px;height:240px;overflow:hidden;
    background:radial-gradient(ellipse at 50% 45%,var(--cream-light) 30%,var(--cream-dark) 100%)}
  .banner-one{top:23px}.banner-two{top:275px}.banner-three{top:527px}
  .banner svg.photos{position:absolute;inset:0}
  .content{position:absolute;left:0;top:0;width:630px;height:240px;text-align:center}
  .brand{position:absolute;top:26px;left:0;width:630px;display:flex;justify-content:center;align-items:center;gap:6px;
    font-family:"Roboto Slab",serif;font-weight:700;font-size:17px;color:var(--accent-red)}
  .brand-dot{width:12px;height:12px;border-radius:50%;background:var(--accent-red)}
  .brand-sub{position:absolute;top:52px;left:0;width:630px;font-family:"Roboto Slab",serif;font-weight:700;
    font-size:10px;color:var(--accent-red);letter-spacing:.5px}
  .kicker{position:absolute;top:82px;left:0;width:630px;font-family:"Lobster",cursive;font-size:18px;color:var(--accent-red)}
  .headline{position:absolute;top:112px;left:0;width:630px;font-family:"Roboto Slab",serif;font-weight:700;
    font-size:29px;color:var(--ink-green);line-height:1}
  .tagline{position:absolute;top:148px;left:0;width:630px;font-family:"Roboto",sans-serif;font-size:12.5px;color:var(--ink)}
  .date-row{position:absolute;top:170px;left:0;width:630px;height:32px}
  .date-row svg{position:absolute;left:0;top:0}
  .date{position:absolute;left:0;top:4px;width:630px;font-family:"Roboto Slab",serif;font-size:17px;color:#fff;
    display:flex;justify-content:center;align-items:center;gap:6px;padding-left:2px}
  .info{position:absolute;top:210px;left:0;width:630px;font-family:"Roboto",sans-serif;font-size:12.5px;color:var(--ink);
    display:flex;justify-content:center;align-items:center;gap:4px}
  .info .url{font-weight:400;color:var(--ink-green);font-family:"Roboto Slab",serif;font-weight:700;font-size:12px}
  .label{position:absolute;left:905px;width:240px;font-family:"Roboto",sans-serif;font-size:14px;color:var(--label);
    transform:rotate(-90deg);transform-origin:left top;text-align:center}
  .label-one{top:263px}.label-two{top:515px}.label-three{top:767px}
</style>
</head>
<body>
<div class="board">

  <section class="banner banner-one">
    <svg class="photos" width="630" height="240" viewBox="0 0 630 240">
      <defs>
        <linearGradient id="saladGrad" x1="0" y1="0" x2="0" y2="1">
          <stop offset="0" stop-color="#6f9a3a"/><stop offset=".55" stop-color="#b9a03a"/><stop offset="1" stop-color="#4a1f3c"/>
        </linearGradient>
        <linearGradient id="nightGrad" x1="0" y1="0" x2="0" y2="1">
          <stop offset="0" stop-color="#1c2b55"/><stop offset=".5" stop-color="#3a3550"/><stop offset="1" stop-color="#8a5a30"/>
        </linearGradient>
      </defs>
      <path role="img" aria-label="Photo of a fresh fig, greens and beet salad" fill="url(#saladGrad)" d="M0 0H97Q135 120 92 240H0Z"/>
      <path role="img" aria-label="Photo of guests dining outdoors under string lights at night" fill="url(#nightGrad)" d="M511 0H630V240H534Q485 120 511 0Z"/>
    </svg>
    <div class="content">
      <div class="brand"><span class="brand-dot"></span>Brimful Maple FQ</div>
      <div class="brand-sub">Fernquay County</div>
      <div class="kicker">Design We’re Back!</div>
      <div class="headline">The Crumb Of Maple Is Back!</div>
      <div class="tagline">Fernquay County’s Premier Food, Wine and Brew Event</div>
      <div class="date-row">
        <svg width="630" height="32" viewBox="0 0 630 32">
          <polygon points="206,2 424,2 414,16 424,30 206,30 216,16" fill="var(--accent-red)"/>
          <g fill="var(--accent-red)" stroke="#fff" stroke-width="2"><circle cx="181" cy="16" r="14"/><circle cx="450" cy="16" r="14"/></g>
          <g stroke="#fff" stroke-width="2.5" stroke-linecap="round"><path d="M174 8L188 24M188 8L174 24M443 8L457 24M457 8L443 24"/></g>
        </svg>
        <div class="date"><svg width="14" height="13" viewBox="0 0 14 13"><rect x="0" y="2" width="14" height="11" fill="#fff"/><rect x="2" y="6" width="3" height="2" fill="var(--accent-red)"/><rect x="6" y="6" width="3" height="2" fill="var(--accent-red)"/><rect x="10" y="6" width="2" height="2" fill="var(--accent-red)"/><rect x="2" y="9" width="3" height="2" fill="var(--accent-red)"/><rect x="6" y="9" width="3" height="2" fill="var(--accent-red)"/></svg>AUGUST 14TH 2022</div>
      </div>
      <div class="info">Vendor and ticket info at <svg width="11" height="11" viewBox="0 0 12 12"><circle cx="6" cy="6" r="5" fill="none" stroke="#333"/><path d="M1 6H11M6 1V11" stroke="#333"/></svg> <span class="url">brimfulmaplefq.com</span></div>
    </div>
  </section>

  <section class="banner banner-two">
    <svg class="photos" width="630" height="240" viewBox="0 0 630 240">
      <defs>
        <linearGradient id="bottleGrad" x1="0" y1="0" x2="0" y2="1">
          <stop offset="0" stop-color="#e08a4a"/><stop offset=".4" stop-color="#8a4a2a"/><stop offset="1" stop-color="#1c1c22"/>
        </linearGradient>
        <linearGradient id="tableGrad" x1="0" y1="0" x2="0" y2="1">
          <stop offset="0" stop-color="#6e8a5a"/><stop offset=".5" stop-color="#3f6a6a"/><stop offset="1" stop-color="#c9c8b0"/>
        </linearGradient>
      </defs>
      <path role="img" aria-label="Photo of rows of wine bottles with copper caps" fill="url(#bottleGrad)" d="M0 0H97Q135 120 92 240H0Z"/>
      <path role="img" aria-label="Photo of a set table with green glasses and lemons" fill="url(#tableGrad)" d="M511 0H630V240H534Q485 120 511 0Z"/>
    </svg>
    <div class="content">
      <div class="brand"><span class="brand-dot"></span>Brimful Maple FQ</div>
      <div class="brand-sub">Fernquay County</div>
      <div class="kicker">Vendors be a part of the event</div>
      <div class="headline">The Crumb of Maple is Back!</div>
      <div class="tagline">Fernquay County’s Premier Food, Wine and Brew Event</div>
      <div class="date-row">
        <svg width="630" height="32" viewBox="0 0 630 32">
          <polygon points="206,2 424,2 414,16 424,30 206,30 216,16" fill="var(--accent-red)"/>
          <g fill="var(--accent-red)" stroke="#fff" stroke-width="2"><circle cx="181" cy="16" r="14"/><circle cx="450" cy="16" r="14"/></g>
          <g stroke="#fff" stroke-width="2.5" stroke-linecap="round"><path d="M174 8L188 24M188 8L174 24M443 8L457 24M457 8L443 24"/></g>
        </svg>
        <div class="date"><svg width="14" height="13" viewBox="0 0 14 13"><rect x="0" y="2" width="14" height="11" fill="#fff"/><rect x="2" y="6" width="3" height="2" fill="var(--accent-red)"/><rect x="6" y="6" width="3" height="2" fill="var(--accent-red)"/><rect x="10" y="6" width="2" height="2" fill="var(--accent-red)"/><rect x="2" y="9" width="3" height="2" fill="var(--accent-red)"/><rect x="6" y="9" width="3" height="2" fill="var(--accent-red)"/></svg>AUGUST 14TH 2020</div>
      </div>
      <div class="info">Vendors sign up today &amp; Vendor info at <svg width="11" height="11" viewBox="0 0 12 12"><circle cx="6" cy="6" r="5" fill="none" stroke="#333"/><path d="M1 6H11M6 1V11" stroke="#333"/></svg> <span class="url">brimfulmaplefq.com</span></div>
    </div>
  </section>

  <section class="banner banner-three">
    <svg class="photos" width="630" height="240" viewBox="0 0 630 240">
      <defs>
        <linearGradient id="settingGrad" x1="0" y1="0" x2="1" y2="1">
          <stop offset="0" stop-color="#d9cfb8"/><stop offset=".5" stop-color="#8a3a55"/><stop offset="1" stop-color="#3f6a3a"/>
        </linearGradient>
        <linearGradient id="plateGrad" x1="0" y1="0" x2="0" y2="1">
          <stop offset="0" stop-color="#4f7a3a"/><stop offset=".5" stop-color="#6a3a3a"/><stop offset="1" stop-color="#2a3a2a"/>
        </linearGradient>
      </defs>
      <path role="img" aria-label="Photo of a long banquet table with glasses and flowers" fill="url(#settingGrad)" d="M0 0H97Q135 120 92 240H0Z"/>
      <path role="img" aria-label="Photo of a plated salad with cured ham and greens" fill="url(#plateGrad)" d="M511 0H630V240H534Q485 120 511 0Z"/>
    </svg>
    <div class="content">
      <div class="brand"><span class="brand-dot"></span>Brimful Maple FQ</div>
      <div class="brand-sub">Fernquay County</div>
      <div class="kicker">Sponsor info</div>
      <div class="headline">The Crumb Of Maple</div>
      <div class="tagline">Fernquay County’s Premier Food, Wine and Brew Event</div>
      <div class="date-row">
        <svg width="630" height="32" viewBox="0 0 630 32">
          <polygon points="206,2 424,2 414,16 424,30 206,30 216,16" fill="var(--accent-red)"/>
          <g fill="var(--accent-red)" stroke="#fff" stroke-width="2"><circle cx="181" cy="16" r="14"/><circle cx="450" cy="16" r="14"/></g>
          <g stroke="#fff" stroke-width="2.5" stroke-linecap="round"><path d="M174 8L188 24M188 8L174 24M443 8L457 24M457 8L443 24"/></g>
        </svg>
        <div class="date"><svg width="14" height="13" viewBox="0 0 14 13"><rect x="0" y="2" width="14" height="11" fill="#fff"/><rect x="2" y="6" width="3" height="2" fill="var(--accent-red)"/><rect x="6" y="6" width="3" height="2" fill="var(--accent-red)"/><rect x="10" y="6" width="2" height="2" fill="var(--accent-red)"/><rect x="2" y="9" width="3" height="2" fill="var(--accent-red)"/><rect x="6" y="9" width="3" height="2" fill="var(--accent-red)"/></svg>AUGUST 14TH 2022</div>
      </div>
      <div class="info">Check out our great Sponsorship opportunities at <svg width="11" height="11" viewBox="0 0 12 12"><circle cx="6" cy="6" r="5" fill="none" stroke="#333"/><path d="M1 6H11M6 1V11" stroke="#333"/></svg> <span class="url">brimfulmaplefq.com</span></div>
    </div>
  </section>

  <div class="label label-one">Banner One</div>
  <div class="label label-two">Banner Two</div>
  <div class="label label-three">Banner Three</div>
</div>
</body>
</html>
```